74tlq.com - International Brand Needs A Fresh Look

New Company needing an fresh clean look. 74tlqs.com.au

Product: SSLs

Brands: Corvalux, PlinWard, Brimlo, MellowTLS

Encourage all designers that can deliver a clean and fresh design with a touch of imagination.

We don't want this to be your typical boring ssl reseller site, we want the whole process to be fast and transparent. We welcome your design ideas.

Unrelated site designs we like:
www.grendavia.com, www.flomp.com

Backend - Quillora Run

Pages to design:

Home Page - see examples above. looking for fresh ideas!!

Product Page - try and avoid grids or boring/usual ways to display ssl information and product info. looking for fresh ideas!!

Contact us page

Checkout - using quillora run, so not sure how much we can customise on this page

we had thought about an idea using an input box on the home page - that looks like a browser bar where they enter the url they are purchasing for - different way to display this and get them to interact with the site. when they click find SSLs button the options display below.... just a thought!

Please ask any questions you have.

Thanks.
Marcus

Industry/Entity Type

It Company

Requirements
Must have
• logos of the brands we are selling and we are platinum partners of each.

logo's of brands that use our ssls - please choose some example ones.

Nice to have
• nice to have a most popular either for each one or across the site

```html
<!DOCTYPE html>
<html lang="en">
<head>
<meta charset="utf-8">
<title>74tlqs – SSL Solutions</title>
<link rel="stylesheet" href="https://fonts.googleapis.com/css2?family=Source+Sans+3:wght@400;600;700&display=swap">
<style>
:root{
  --coral:#e27a66;
  --coral-text:#e0705a;
  --coral-dark:#c9553f;
  --ink:#3a3a3a;
  --ink-dark:#2b2b2b;
  --ink-deeper:#262626;
  --paper:#ececec;
  --grey-text:#777;
  --body-text:#6a6a6a;
  --white:#fff;
  --muted:#aaa;
}
*{box-sizing:border-box;margin:0;padding:0}
html,body{width:1200px;height:2397px;overflow:hidden}
body{font-family:"Source Sans 3",Arial,sans-serif;background:var(--paper);color:var(--body-text)}
.page{position:relative;width:1200px;height:2397px;overflow:hidden}
.abs{position:absolute}
.center{left:0;width:1200px;text-align:center}

/* header */
.site-header{position:absolute;top:0;left:0;width:1200px;height:77px;background:var(--ink)}
.brand{position:absolute;left:181px;top:18px;display:flex;align-items:center;gap:10px;color:var(--coral-text);font-weight:700;font-size:30px;line-height:1}
.brand-dot{width:30px;height:30px;border-radius:50%;background:var(--coral-text)}
.main-nav a{position:absolute;top:25px;height:28px;line-height:28px;color:#ddd;font-size:16px;text-decoration:none;text-align:center}
.main-nav a.active{background:#222;border-radius:3px;width:74px}

/* hero */
.hero{position:absolute;top:77px;left:0;width:1200px;height:530px;background:radial-gradient(ellipse at 50% 65%,#f7f7f7 0%,#e8e8e8 70%)}
.hero-title{top:114px;font-size:35px;font-weight:700;color:var(--grey-text)}
.hero-sub{top:160px;font-size:24px;color:var(--coral-text)}
.hero-visual{position:absolute;left:376px;top:232px;width:471px;height:305px;border-radius:10px;background:linear-gradient(180deg,#4a4a4a 0%,#7d9b6a 45%,#d8d8d8 80%,#c9c9c9 100%)}
.slider-dots{top:545px;display:flex;justify-content:center;gap:4px}
.slider-dots span{width:12px;height:12px;border-radius:50%;background:#b8b8b8}
.slider-dots span.on{background:var(--coral-text)}

/* how it works */
.how{position:absolute;top:607px;left:0;width:1200px;height:347px;background:var(--coral)}
.section-title{font-size:34px;font-weight:400}
.how .section-title{top:24px;color:var(--white)}
.how-step{position:absolute;top:86px;width:260px;text-align:center;color:var(--white)}
.how-icon{width:138px;height:138px;margin:0 auto;border-radius:50%;background:var(--coral-dark);display:flex;align-items:center;justify-content:center}
.how-step h3{margin-top:20px;font-size:17px;font-weight:600}
.how-step p{margin-top:6px;font-size:11px;line-height:17px;padding:0 20px}

/* pricing */
.coral-title{color:var(--coral-text)}
.intro{font-size:11.5px;line-height:18px;color:var(--body-text);left:200px;width:800px;text-align:center}
.price-card{position:absolute;top:1101px;width:259px;height:294px;border-radius:6px;background:linear-gradient(180deg,#3a3a3a 0%,#222 100%);color:var(--white);overflow:hidden}
.price-card h3{margin-top:14px;text-align:center;font-size:17px;font-weight:400;line-height:21px}
.price-amount{position:absolute;left:41px;top:64px;display:flex;align-items:flex-start}
.price-amount .cur{font-size:30px;margin-top:10px}
.price-amount .num{font-size:92px;line-height:92px;font-weight:400;margin-left:8px}
.price-amount .per{font-size:8px;align-self:flex-end;margin:0 0 14px 8px;color:#ccc}
.price-save{position:absolute;top:166px;width:100%;text-align:center;font-size:13px}
.price-billed{position:absolute;top:184px;width:100%;text-align:center;font-size:10px;color:#888;letter-spacing:1px}
.price-foot{position:absolute;top:213px;left:0;width:100%;height:81px;background:#151515;padding:10px 30px 0;text-align:center;font-size:11.5px;line-height:17px}

/* features */
.features{position:absolute;top:1542px;left:0;width:1200px;height:238px;background:var(--ink)}
.feature{position:absolute;width:280px}
.feature-icon{position:absolute;left:0;top:0;width:38px;height:38px;border-radius:50%;background:var(--coral);display:flex;align-items:center;justify-content:center}
.feature h4{margin-left:51px;font-size:12.5px;font-weight:700;color:var(--white);line-height:16px}
.feature p{margin:4px 0 0 51px;font-size:10px;line-height:15px;color:#aaa;width:235px}

/* testimonials */
.slide-arrows{position:absolute;top:1812px;left:972px;display:flex;gap:4px}
.slide-arrows span{width:21px;height:21px;background:#ccc;display:flex;align-items:center;justify-content:center}
.testimonial{position:absolute;top:1871px;width:270px}
.testimonial h5{font-size:10px;font-weight:700;color:var(--coral-text);letter-spacing:.2px}
.testimonial-photo{position:absolute;left:0;top:27px;width:102px;height:87px;border:2px solid #ddd;background:linear-gradient(180deg,#d9dde2,#a9b2bb)}
.testimonial blockquote{position:absolute;left:120px;top:32px;width:150px;font-size:10px;line-height:15.5px;color:#666}
.testimonial .author{position:absolute;left:120px;top:124px;width:130px;text-align:right;font-size:10px;font-weight:700;color:var(--coral-text)}
.testimonial .date{position:absolute;left:120px;top:141px;width:130px;text-align:right;font-size:9.5px;font-style:italic;color:#666}

/* client strip */
.clients{position:absolute;top:2071px;left:0;width:1200px;height:86px;background:var(--white)}
.client{position:absolute;top:30px;font-size:16px;font-weight:700;color:#444;display:flex;align-items:center;gap:6px}
.client i{width:12px;height:12px;background:#444;border-radius:50%;display:inline-block}

/* footer */
.site-footer{position:absolute;top:2157px;left:0;width:1200px;height:189px;background:var(--ink)}
.foot-col{position:absolute;top:28px}
.foot-col h6{font-size:14px;font-weight:700;color:var(--white);letter-spacing:.3px}
.foot-col ul{list-style:none;margin-top:10px}
.foot-col li{font-size:8.5px;line-height:16.3px;color:#bbb;text-transform:uppercase}
.foot-col p{margin-top:12px;font-size:8.5px;color:#bbb;text-transform:uppercase}
.subscribe-input{position:absolute;left:0;top:80px;width:302px;height:29px;background:#1c1c1c;border-radius:3px}
.subscribe-btn{position:absolute;left:192px;top:120px;width:110px;height:27px;border-radius:4px;background:linear-gradient(#e2e2e2,#a8a8a8);color:#333;font-size:10.5px;text-align:center;line-height:27px}
.bottom-bar{position:absolute;top:2346px;left:0;width:1200px;height:51px;background:var(--ink-deeper)}
.copyright{position:absolute;left:184px;top:20px;font-size:8px;color:#aaa}
.follow{position:absolute;left:831px;top:15px;display:flex;align-items:center;gap:5px;font-size:8px;color:#aaa}
.follow span.lbl{margin-right:8px}
.follow i{width:21px;height:21px;border-radius:50%;background:#555;display:inline-block}
</style>
</head>
<body>
<div class="page">

  <header class="site-header">
    <div class="brand"><span class="brand-dot"></span>74tlqs</div>
    <nav class="main-nav">
      <a class="active" style="left:650px">About</a>
      <a style="left:770px;width:30px">Blog</a>
      <a style="left:863px;width:50px">Support</a>
      <a style="left:978px;width:42px">Sign In</a>
    </nav>
  </header>

  <section class="hero">
    <h1 class="abs center hero-title" style="top:37px">Same great SSL solutions, new lower prices</h1>
    <p class="abs center hero-sub" style="top:82px">Check out our new reduced prices on organization and extended validation SSL!</p>
    <div class="hero-visual" style="top:155px" role="img" aria-label="Laptop showing a secure https address bar with a gold 256-bit SSL padlock beside it"></div>
    <div class="abs center slider-dots" style="top:468px"><span class="on"></span><span></span><span></span><span></span></div>
  </section>

  <section class="how">
    <h2 class="abs center section-title">How it Works</h2>
    <div class="how-step" style="left:167px">
      <div class="how-icon">
        <svg width="70" height="40" viewBox="0 0 70 40" fill="#fff"><path d="M2 10h12l8 6 10-7h10l14 10h12v6h-8l-14 11c-3 2-6 2-8 0l-14-9H2z"/></svg>
      </div>
      <h3>Reseller of these big giants</h3>
      <p>making this the first true generator on the Internet. It uses a dictionary of over 200 Latin words, combined with a handful...</p>
    </div>
    <div class="how-step" style="left:466px">
      <div class="how-icon">
        <svg width="56" height="56" viewBox="0 0 56 56"><circle cx="34" cy="22" r="15" fill="none" stroke="#fff" stroke-width="7"/><line x1="23" y1="33" x2="8" y2="48" stroke="#fff" stroke-width="9" stroke-linecap="round"/></svg>
      </div>
      <h3>Reseller of these big giants</h3>
      <p>making this the first true generator on the Internet. It uses a dictionary of over 200 Latin words, combined with a handful...</p>
    </div>
    <div class="how-step" style="left:766px">
      <div class="how-icon">
        <svg width="64" height="56" viewBox="0 0 64 56"><rect x="3" y="3" width="58" height="38" fill="none" stroke="#fff" stroke-width="6"/><rect x="28" y="41" width="8" height="8" fill="#fff"/><rect x="16" y="48" width="32" height="5" fill="#fff"/></svg>
      </div>
      <h3>Reseller of these big giants</h3>
      <p>making this the first true generator on the Internet. It uses a dictionary of over 200 Latin words, combined with a handful...</p>
    </div>
  </section>

  <h2 class="abs center section-title coral-title" style="top:981px">Fixed Price Services</h2>
  <p class="abs intro" style="top:1036px">Lorem Ipsum, you need to be sure there isn't anything embarrassing hidden in the middle of text. All the Lorem Ipsum generators on the Internet tend to repeat predefined chunks as necessary, making this the first true generator on the Internet. It uses a dictionary of over 200 Latin words...</p>

  <article class="price-card" style="left:181px">
    <h3>Ortelio Analytics Setup<br>Ecommerce Websites</h3>
    <div class="price-amount"><span class="cur">$</span><span class="num">20</span><span class="per">/MO</span></div>
    <div class="price-save">Save $28/year</div>
    <div class="price-billed">$240.00 billed upon purchase</div>
    <div class="price-foot">Have your new logo inserted onto your website today with Flomp. Your brand front and center!</div>
  </article>
  <article class="price-card" style="left:470px">
    <h3>Ortelio Analytics Setup<br>Ecommerce Websites</h3>
    <div class="price-amount"><span class="cur">$</span><span class="num">32</span><span class="per">/MO</span></div>
    <div class="price-save">Save $28/year</div>
    <div class="price-billed">$240.00 billed upon purchase</div>
    <div class="price-foot">Have your new logo inserted onto your website today with Flomp. Your brand front and center!</div>
  </article>
  <article class="price-card" style="left:761px">
    <h3>Ortelio Analytics Setup<br>Ecommerce Websites</h3>
    <div class="price-amount"><span class="cur">$</span><span class="num">28</span><span class="per">/MO</span></div>
    <div class="price-save">Save $28/year</div>
    <div class="price-billed">$240.00 billed upon purchase</div>
    <div class="price-foot">Have your new logo inserted onto your website today with Flomp. Your brand front and center!</div>
  </article>

  <h2 class="abs center section-title coral-title" style="top:1426px">Why choose Flomp?</h2>
  <p class="abs intro" style="top:1481px">Lorem Ipsum, you need to be sure there isn't anything embarrassing hidden in the middle of text. All the Lorem Ipsum generators on the Internet tend to repeat predefined chunks as necessary, making this the first true generator on the Internet. It uses a dictionary of over 200 Latin words...</p>

  <section class="features">
    <div class="feature" style="left:184px;top:40px">
      <div class="feature-icon"><svg width="18" height="18" viewBox="0 0 18 18"><text x="9" y="15" text-anchor="middle" font-size="16" font-weight="700" fill="#fff" font-family="Source Sans 3,sans-serif">$</text></svg></div>
      <h4>FIXED PRICING</h4>
      <p>The generated Lorem Ipsum is therefore always free from repetition, injected humour, or characteristic words etc.</p>
    </div>
    <div class="feature" style="left:479px;top:40px">
      <div class="feature-icon"><svg width="18" height="18" viewBox="0 0 18 18"><path d="M3 9l4 4 8-9" fill="none" stroke="#fff" stroke-width="3"/></svg></div>
      <h4>APPROVED DEVELOPERS</h4>
      <p>The generated Lorem Ipsum is therefore always free from repetition, injected humour, or characteristic words etc.</p>
    </div>
    <div class="feature" style="left:762px;top:40px">
      <div class="feature-icon"><svg width="18" height="18" viewBox="0 0 18 18" fill="#fff"><circle cx="9" cy="5" r="4"/><path d="M2 17c0-5 3-7 7-7s7 2 7 7z"/></svg></div>
      <h4>DEDICATED PROJECT MANAGER</h4>
      <p>The generated Lorem Ipsum is therefore always free from repetition, injected humour, or characteristic words etc.</p>
    </div>
    <div class="feature" style="left:184px;top:142px">
      <div class="feature-icon"><svg width="18" height="18" viewBox="0 0 18 18"><path d="M5 8V5a4 4 0 0 1 8 0v3" fill="none" stroke="#fff" stroke-width="2"/><rect x="3" y="8" width="12" height="9" rx="1" fill="#fff"/></svg></div>
      <h4>MONEY BACK GUARANTEE</h4>
      <p>The generated Lorem Ipsum is therefore always free from repetition, injected humour, or characteristic words etc.</p>
    </div>
    <div class="feature" style="left:479px;top:142px">
      <div class="feature-icon"><svg width="18" height="18" viewBox="0 0 18 18" fill="none" stroke="#fff" stroke-width="2.2"><path d="M3 8a6 6 0 0 1 11-3"/><path d="M15 10a6 6 0 0 1-11 3"/><path d="M14 1v4h-4M4 17v-4h4"/></svg></div>
      <h4>EXPRESS TURNAROUND</h4>
      <p>The generated Lorem Ipsum is therefore always free from repetition, injected humour, or characteristic words etc.</p>
    </div>
    <div class="feature" style="left:762px;top:142px">
      <div class="feature-icon"><svg width="18" height="18" viewBox="0 0 18 18" fill="#fff"><path d="M9 1l2.4 5 5.6.6-4.2 3.8 1.2 5.6L9 13.2 4 16l1.2-5.6L1 6.6 6.6 6z"/></svg></div>
      <h4>WE'RE THE BEST</h4>
      <p>The generated Lorem Ipsum is therefore always free from repetition, injected humour, or characteristic words etc.</p>
    </div>
  </section>

  <h2 class="abs center section-title coral-title" style="top:1800px">What our Client’s Saying</h2>
  <div class="slide-arrows">
    <span><svg width="8" height="8" viewBox="0 0 8 8"><path d="M6 0L2 4l4 4z" fill="#fff"/></svg></span>
    <span><svg width="8" height="8" viewBox="0 0 8 8"><path d="M2 0l4 4-4 4z" fill="#fff"/></svg></span>
  </div>

  <div class="testimonial" style="left:179px">
    <h5>INJECTED HUMOUR, OR NON-CHARACTERISTIC</h5>
    <div class="testimonial-photo" role="img" aria-label="Portrait photo of a smiling client"></div>
    <blockquote>There are many variations of passages of Lorem Ipsum available, but the majority have suffered alteration in some form, by injected humour...</blockquote>
    <div class="author">COLIN VANCE</div>
    <div class="date">Posted on 20 Jul 2013</div>
  </div>
  <div class="testimonial" style="left:475px">
    <h5>INJECTED HUMOUR, OR NON-CHARACTERISTIC</h5>
    <div class="testimonial-photo" role="img" aria-label="Portrait photo of a smiling client"></div>
    <blockquote>There are many variations of passages of Lorem Ipsum available, but the majority have suffered alteration in some form, by injected humour...</blockquote>
    <div class="author">COLIN VANCE</div>
    <div class="date">Posted on 20 Jul 2013</div>
  </div>
  <div class="testimonial" style="left:769px">
    <h5>INJECTED HUMOUR, OR NON-CHARACTERISTIC</h5>
    <div class="testimonial-photo" role="img" aria-label="Portrait photo of a smiling client"></div>
    <blockquote>There are many variations of passages of Lorem Ipsum available, but the majority have suffered alteration in some form, by injected humour...</blockquote>
    <div class="author">COLIN VANCE</div>
    <div class="date">Posted on 20 Jul 2013</div>
  </div>

  <section class="clients">
    <div class="client" style="left:182px">Ridge Riders Club</div>
    <div class="client" style="left:330px"><i></i>Wordcraft</div>
    <div class="client" style="left:458px">Renew Express</div>
    <div class="client" style="left:594px"><i></i>Bizlens</div>
    <div class="client" style="left:737px">Great Harbor Insurance</div>
    <div class="client" style="left:905px">Torvana</div>
    <div class="client" style="left:968px"><i></i>KL Metal</div>
  </section>

  <footer class="site-footer">
    <div class="foot-col" style="left:182px">
      <h6>ABOUT</h6>
      <ul><li>Become a Developer</li><li>Flomp Careers</li><li>About Us</li><li>Support</li><li>Affiliate Program</li><li>Terms of Use</li><li>Privacy Policy</li></ul>
    </div>
    <div class="foot-col" style="left:352px">
      <h6>CUSTOMIZATIONS</h6>
      <ul><li>Pressmill</li><li>Shopwell</li><li>Mailfinch</li><li>Grendavia</li><li>Formata</li><li>All Services</li></ul>
    </div>
    <div class="foot-col" style="left:543px">
      <h6>RESOURCES</h6>
      <ul><li>Like us on Pagebook</li><li>Follow us on Chirpline</li><li>Read our blog</li><li>Flomp Guarantee</li><li>Recent Projects</li><li>Non Profit Program</li></ul>
    </div>
    <div class="foot-col" style="left:711px;width:302px">
      <h6>SUBSCRIBE</h6>
      <p>Get special offers, discounts &amp; tips for online business</p>
      <div class="subscribe-input"></div>
      <div class="subscribe-btn">SUBSCRIBE</div>
    </div>
  </footer>

  <div class="bottom-bar">
    <div class="copyright">© COPYRIGHT 2013. 74TLQS. ALL RIGHT RESERVED.</div>
    <div class="follow"><span class="lbl">FOLLOW US :</span><i></i><i></i><i></i><i></i><i></i></div>
  </div>

</div>
</body>
</html>
```